Lorvex Tilo medical cannibis cultivation company

tag - Tilo rise
Lorvex Tilo medical cannabis cultivation - logo is selected- can we please see bold examples with our selection. We are mainly dealing with medical companies and professionals. We would like to be stand out in the crowd with our designs. Welcome any and all attempts. Thanks

Target Market(s)

Medical and Professional

Industry/Entity Type

Medical And Science

Font styles to use
Sans Serif

Colors

Designer to choose colors to be used in the design.

Requirements
Must have
• Bright colour and be bold- Love the teal and magenta that is currently on the dark background design.
Nice to have
• shading and the 3D affect- The shadowed appearance.
Should not have
• Anything related to illegal activity or un professional manners

```html
<!DOCTYPE html>
<html lang="en">
<head>
<meta charset="utf-8">
<title>Lorvex Tilo – Business Card</title>
<link rel="stylesheet" href="https://fonts.googleapis.com/css2?family=Marcellus&family=Tinos&display=swap">
<style>
  :root {
    --page: #e9e9e9;
    --card: #000000;
    --magenta: #9d4a96;
    --teal: #00ade6;
    --ring: #8a8d91;
    --white: #ffffff;
  }
  * { margin: 0; padding: 0; box-sizing: border-box; }
  html, body {
    width: 1125px;
    height: 1200px;
    overflow: hidden;
    background: var(--page);
  }
  .canvas {
    position: relative;
    width: 1125px;
    height: 1200px;
  }
  .card {
    position: absolute;
    left: 150px;
    width: 826px;
    height: 471px;
    border-radius: 24px;
    background: var(--card);
    overflow: hidden;
    box-shadow: 0 14px 30px rgba(0,0,0,0.28), 0 3px 6px rgba(0,0,0,0.2);
  }
  .card--front { top: 98px; }
  .card--back { top: 631px; }

  /* Front */
  .band {
    position: absolute;
    top: 80px;
    height: 309px;
  }
  .band--magenta { left: 0; width: 826px; background: var(--magenta); }
  .band--teal { left: 600px; width: 226px; background: var(--teal); }

  .emblem {
    position: absolute;
    left: 419px;
    top: 67px;
    width: 330px;
    height: 330px;
    border-radius: 50%;
    background: var(--card);
    border: 8px solid var(--ring);
    box-shadow: 0 0 18px rgba(0,0,0,0.55);
    display: flex;
    align-items: center;
    justify-content: center;
  }
  .emblem__name {
    font-family: "Marcellus", serif;
    font-size: 34px;
    letter-spacing: 1px;
    color: var(--teal);
    text-transform: uppercase;
  }

  .contact {
    position: absolute;
    left: 64px;
    top: 128px;
    color: var(--white);
  }
  .contact__name {
    font-family: "Marcellus", serif;
    font-size: 29px;
    font-weight: 700;
    line-height: 1;
    letter-spacing: 0.5px;
    -webkit-text-stroke: 0.6px var(--white);
  }
  .contact__role {
    font-family: "Marcellus", serif;
    font-size: 19px;
    line-height: 1.2;
    margin-top: 4px;
    -webkit-text-stroke: 0.4px var(--white);
  }
  .contact__address {
    font-family: "Tinos", serif;
    font-size: 19px;
    line-height: 1.3;
    margin-top: 16px;
  }
  .contact__list {
    list-style: none;
    margin-top: 14px;
    font-family: "Tinos", serif;
    font-size: 19px;
    line-height: 1.4;
  }
  .contact__list li {
    display: flex;
    align-items: center;
    gap: 11px;
  }
  .contact__icon {
    width: 18px;
    height: 18px;
    fill: var(--white);
    flex: none;
  }

  /* Back */
  .mark-circle {
    position: absolute;
    left: 327px;
    top: 114px;
    width: 172px;
    height: 172px;
    border-radius: 50%;
    border: 6px solid var(--ring);
  }
  .wordmark {
    position: absolute;
    left: 0;
    width: 826px;
    top: 282px;
    text-align: center;
    font-family: "Marcellus", serif;
    font-size: 50px;
    line-height: 1;
    color: var(--teal);
    text-transform: uppercase;
  }
  .tagline {
    position: absolute;
    left: 0;
    width: 826px;
    top: 342px;
    display: flex;
    align-items: center;
    justify-content: center;
    gap: 8px;
    font-family: "Marcellus", serif;
    font-size: 20px;
    letter-spacing: 2px;
    color: var(--ring);
    text-transform: uppercase;
  }
  .tagline__rule {
    width: 58px;
    height: 2px;
    background: var(--ring);
  }
</style>
</head>
<body>
<main class="canvas">

  <section class="card card--front" aria-label="Business card front">
    <div class="band band--magenta"></div>
    <div class="band band--teal"></div>

    <div class="contact">
      <p class="contact__name">MAREN HOLLIS</p>
      <p class="contact__role">CEO/FOUNDER</p>
      <p class="contact__address">4120 Fernwood Court<br>Juneau, Alaska 34518</p>
      <ul class="contact__list">
        <li>
          <svg class="contact__icon" viewBox="0 0 24 24" aria-hidden="true"><path d="M6.6 10.8a15.1 15.1 0 0 0 6.6 6.6l2.2-2.2a1 1 0 0 1 1-.25 11.4 11.4 0 0 0 3.6.57 1 1 0 0 1 1 1V20a1 1 0 0 1-1 1A17 17 0 0 1 3 4a1 1 0 0 1 1-1h3.5a1 1 0 0 1 1 1c0 1.25.2 2.45.57 3.6a1 1 0 0 1-.25 1z"/></svg>
          <span>612 480 3915</span>
        </li>
        <li>
          <svg class="contact__icon" viewBox="0 0 24 24" aria-hidden="true"><path d="M3 6h18v12H3z" fill="none"/><path d="M3 6l9 7 9-7v12H3z"/><path d="M3 5h18l-9 6.5z"/></svg>
          <span>maren@lorvextilo.com</span>
        </li>
        <li>
          <svg class="contact__icon" viewBox="0 0 24 24" aria-hidden="true"><circle cx="12" cy="12" r="10"/><path d="M8 6c2 1 1 3 3 3s1 3 -1 3-2 3 0 5M15 5c-1 2 1 3 2 4s3 1 3 3" stroke="#9d4a96" stroke-width="1.6" fill="none"/></svg>
          <span>www.lorvextilo.com</span>
        </li>
      </ul>
    </div>

    <div class="emblem">
      <span class="emblem__name">Lorvex Tilo</span>
    </div>
  </section>

  <section class="card card--back" aria-label="Business card back">
    <div class="mark-circle"></div>
    <p class="wordmark">Lorvex Tilo</p>
    <p class="tagline"><span class="tagline__rule"></span>Tilo rise<span class="tagline__rule"></span></p>
  </section>

</main>
</body>
</html>
```